Small Business Broker Business Card Design

A business card design for a small business brokerage, which is a financial service, not unlike real estate brokerage, but for small businesses such as laundromats, pizza shops, restaurants, cleaners etc. The designs should all be simple, more conservative in nature, using the colors and font of the logo. Again, think real estate Brokerage as a business context
Contact Information for Business Card
Name: Glen R. Harlow. Title: Small Business Advisor. Email: g.harlow@bayfieldcapitalworks.example. Mobile: (555) 274-3918. Office: (555) 806-2147. www.bayfieldcapitalworks.example

```html
<!DOCTYPE html>
<html lang="en">
<head>
<meta charset="utf-8">
<title>Bayfield Capital Works – Business Card</title>
<link rel="stylesheet" href="https://fonts.googleapis.com/css2?family=Roboto:wght@400;700;900&family=Roboto+Condensed:wght@400&display=swap">
<style>
  :root {
    --backdrop: #232323;
    --brand-green: #8dc63f;
    --brand-green-deep: #5e9e2c;
    --brand-green-text: #7cbf36;
    --card-white: #ffffff;
    --ink: #1e1e1e;
    --rule: #555555;
  }
  * { box-sizing: border-box; margin: 0; padding: 0; }
  html, body {
    width: 1200px; height: 780px; overflow: hidden;
    background: var(--backdrop);
  }
  .canvas {
    position: relative; width: 1200px; height: 780px;
    display: flex; flex-direction: column; align-items: center; justify-content: center; gap: 40px;
  }
  .card {
    width: 560px; height: 320px; border-radius: 22px;
    position: relative; overflow: hidden;
    box-shadow: 0 14px 30px rgba(0,0,0,.55);
  }

  /* Front */
  .card--front {
    background: var(--brand-green);
    display: flex; flex-direction: column; align-items: center; justify-content: center;
    font-family: "Roboto", Arial, sans-serif;
    text-align: center;
  }
  .brand-mark {
    width: 18px; height: 18px; background: var(--brand-green-deep);
    margin-bottom: 18px;
  }
  .brand-name {
    font-weight: 900; font-size: 30px; letter-spacing: 1.5px;
    text-transform: uppercase; color: var(--brand-green-deep);
    white-space: nowrap;
  }
  .brand-tagline {
    margin-top: 6px; font-weight: 700; font-size: 11.5px; letter-spacing: 2.4px;
    text-transform: uppercase; color: var(--brand-green-deep);
    white-space: nowrap;
  }

  /* Back */
  .card--back {
    background: var(--card-white);
    border-bottom: 4px solid var(--brand-green);
    display: flex; align-items: center; justify-content: center; gap: 22px;
    padding-top: 10px;
  }
  .identity { text-align: right; font-family: "Roboto", Arial, sans-serif; }
  .identity__name {
    font-weight: 700; font-size: 30px; color: var(--brand-green-text); letter-spacing: -.3px; line-height: 1.05;
    white-space: nowrap;
  }
  .identity__title { font-size: 14.5px; color: var(--ink); margin-top: 2px; }
  .divider { width: 1px; height: 96px; background: var(--rule); }
  .contact-list {
    list-style: none; font-family: "Roboto Condensed", "Arial Narrow", sans-serif;
    font-size: 13.5px; color: var(--ink);
  }
  .contact-list li { display: flex; align-items: center; gap: 8px; line-height: 21px; white-space: nowrap; }
  .contact-list svg { width: 13px; height: 13px; flex: none; }
  .icon { fill: none; stroke: var(--brand-green); stroke-width: 1.6; }
  .icon--solid { fill: var(--brand-green); stroke: none; }
</style>
</head>
<body>
<main class="canvas">

  <section class="card card--front" aria-label="Card front">
    <span class="brand-mark" aria-hidden="true"></span>
    <h1 class="brand-name">Bayfield Capital Works, Inc</h1>
    <p class="brand-tagline">Steady guidance to buy or sell a main street firm</p>
  </section>

  <section class="card card--back" aria-label="Card back">
    <div class="identity">
      <h2 class="identity__name">Glen R. Harlow</h2>
      <p class="identity__title">Small Business Advisor</p>
    </div>
    <span class="divider" aria-hidden="true"></span>
    <ul class="contact-list">
      <li>
        <svg viewBox="0 0 14 14" aria-hidden="true"><rect class="icon" x="3.5" y="1" width="7" height="12" rx="1.2"/></svg>
        (555) 274-3918
      </li>
      <li>
        <svg viewBox="0 0 14 14" aria-hidden="true"><path class="icon--solid" d="M3 1.5l2.2 2.6-1.3 1.6c.8 1.8 2.2 3.2 4 4l1.6-1.3 2.6 2.2-1.4 1.9C5.8 12.3 1.7 8.2 1.1 3z"/></svg>
        (555) 806-2147
      </li>
      <li>
        <svg viewBox="0 0 14 14" aria-hidden="true"><circle class="icon" cx="7" cy="7" r="5.6"/><path class="icon" d="M1.4 7h11.2M7 1.4c-2.4 3-2.4 8.2 0 11.2M7 1.4c2.4 3 2.4 8.2 0 11.2"/></svg>
        www.bayfieldcapitalworks.example
      </li>
      <li>
        <svg viewBox="0 0 14 14" aria-hidden="true"><rect class="icon" x="1" y="3" width="12" height="8.5" rx="1"/><path class="icon" d="M1.3 3.4L7 8l5.7-4.6"/></svg>
        g.harlow@bayfieldcapitalworks.example
      </li>
    </ul>
  </section>

</main>
</body>
</html>
```